Oil and Gas Exploration and Production company needs a business card design

We need a business card design using our logo and colors in the logo. We want a mainstream design.

```html
<!DOCTYPE html>
<html lang="en">
<head>
<meta charset="utf-8">
<title>Keldra Oil &amp; Gas – Business Card</title>
<link href="https://fonts.googleapis.com/css2?family=Arimo:wght@400;700&display=swap" rel="stylesheet">
<style>
  :root {
    --ink: #0b0b0b;
    --gold: #cf9a2e;
    --paper: #ffffff;
    --stage: #e9e5df;
    --pattern-dark: #141414;
    --pattern-light: #262626;
  }
  * { box-sizing: border-box; margin: 0; padding: 0; }
  html, body { width: 1200px; height: 995px; overflow: hidden; }
  body {
    background: var(--stage);
    font-family: "Arimo", Arial, sans-serif;
    position: relative;
  }
  .card {
    position: absolute;
    top: 188px;
    width: 354px;
    height: 620px;
    border-radius: 22px;
    overflow: hidden;
    box-shadow: 0 10px 28px rgba(0,0,0,.22);
  }
  .card--back { left: 190px; }
  .card--front { left: 656px; background: var(--paper); }

  .back-pattern {
    position: absolute; inset: 0;
    background: radial-gradient(circle at 50% 45%, var(--pattern-light), var(--pattern-dark) 75%);
  }

  .brand {
    position: absolute; top: 92px; left: 0; right: 0;
    display: flex; align-items: center; justify-content: center; gap: 12px;
  }
  .brand__dot {
    width: 26px; height: 26px; border-radius: 50%;
    background: var(--ink);
  }
  .brand__name {
    font-weight: 700; font-size: 34px; color: var(--ink);
    letter-spacing: .5px;
  }

  .person { position: absolute; top: 240px; left: 44px; }
  .person__name { font-weight: 700; font-size: 26px; color: var(--ink); }
  .person__title { font-size: 17px; color: var(--gold); margin-top: 2px; }

  .contact {
    position: absolute; top: 318px; left: 44px;
    font-size: 17px; line-height: 23px; color: var(--ink);
  }
  .contact__address { margin-bottom: 4px; }
  .contact__row { display: flex; align-items: center; gap: 10px; }
  .contact__row svg { width: 16px; height: 14px; flex: none; }
  .contact__web { margin-top: 10px; letter-spacing: 1.5px; }
  .contact__web .domain { color: var(--gold); }

  .wave { position: absolute; left: 0; bottom: 0; width: 354px; height: 620px; }
</style>
</head>
<body>

  <div class="card card--back">
    <div class="back-pattern" role="img" aria-label="Repeating sunburst pattern in dark grey on black"></div>
  </div>

  <div class="card card--front">
    <div class="brand">
      <span class="brand__dot"></span>
      <span class="brand__name">Keldra Oil &amp; Gas</span>
    </div>

    <div class="person">
      <p class="person__name">Marek Doyle</p>
      <p class="person__title">President &amp; CEO</p>
    </div>

    <div class="contact">
      <p class="contact__address">PO BOX 48, Harbour Road<br>5th Lane, Westmoor</p>
      <p class="contact__row">
        <svg viewBox="0 0 16 14" aria-hidden="true"><path d="M1 5c0-3 14-3 14 0v1h-4V4H5v2H1z M4 7h8l2 6H2z" fill="var(--gold)"/></svg>
        (204) 555 0186
      </p>
      <p class="contact__row">
        <svg viewBox="0 0 16 14" aria-hidden="true"><rect x="1" y="2" width="14" height="10" fill="var(--gold)"/><path d="M1 2l7 6 7-6" stroke="#fff" stroke-width="1.4" fill="none"/></svg>
        hello@keldramail.com
      </p>
      <p class="contact__web">www.<span class="domain">keldraenergy</span>.com</p>
    </div>

    <svg class="wave" viewBox="0 0 354 620" aria-hidden="true">
      <path d="M0 560 C 130 556, 250 470, 300 395 C 270 470, 150 540, 0 545 Z" fill="var(--gold)"/>
      <path d="M0 620 L0 578 C 140 575, 270 480, 354 345 L354 620 Z" fill="var(--ink)"/>
      <path d="M0 596 C 150 592, 285 495, 354 372" stroke="var(--paper)" stroke-width="6" fill="none"/>
    </svg>
  </div>

</body>
</html>
```